Local fast-growing company in the service sector

We are looking for a modern business card design, which should also appear on our letterheads

Target Market(s)

Private and industrial sectors

Contact Information for Business Card

Vorname Name
Kellberger Str. 18
73614 Lindenfeld
Tel.: 07146-839214-0
Name@agentur-kvtl.de

Colors
9d9d9d
919191
aaaaaa

Requirements
Must have
• The logo (file) in silver

```html
<!DOCTYPE html>
<html lang="de">
<head>
<meta charset="utf-8">
<title>KVTL Visitenkarte</title>
<link rel="stylesheet" href="https://fonts.googleapis.com/css2?family=Open+Sans:wght@400;700&display=swap">
<style>
  :root {
    --backdrop: #2b2b2b;
    --card: #ffffff;
    --card-shade: #e6e6e6;
    --silver: #9d9d9d;
    --silver-dark: #919191;
    --silver-light: #aaaaaa;
    --map-tint: #ececec;
    --ink: #111111;
    --rule: #b5b5b5;
  }
  * { box-sizing: border-box; margin: 0; padding: 0; }
  html, body {
    width: 1200px;
    height: 716px;
    overflow: hidden;
    background: var(--backdrop);
    font-family: "Open Sans", Arial, sans-serif;
  }
  .canvas {
    position: relative;
    width: 1200px;
    height: 716px;
    display: flex;
    align-items: center;
    justify-content: center;
    gap: 60px;
  }
  .business-card {
    position: relative;
    width: 510px;
    height: 330px;
    background: var(--card);
    overflow: hidden;
  }
  /* Front side */
  .card-front .world-map {
    position: absolute;
    left: 40px;
    top: 30px;
    width: 430px;
    height: 250px;
    border-radius: 40% 45% 40% 50%;
    background: radial-gradient(ellipse at center, var(--map-tint) 0%, #f6f6f6 60%, var(--card) 100%);
  }
  .card-front .brand {
    position: absolute;
    left: 0;
    right: 0;
    top: 118px;
    text-align: center;
    color: var(--silver);
  }
  .brand-name {
    display: block;
    font-weight: 700;
    font-size: 64px;
    line-height: 1;
    letter-spacing: 2px;
  }
  .brand-web {
    display: block;
    font-weight: 700;
    font-size: 22px;
    line-height: 1.3;
    letter-spacing: 1px;
  }
  /* Back side */
  .card-back {
    background: linear-gradient(135deg, var(--card) 0%, #f4f4f4 55%, var(--card-shade) 100%);
    text-align: center;
    color: var(--ink);
  }
  .holder-name {
    position: absolute;
    top: 46px;
    left: 0;
    right: 0;
    font-weight: 700;
    font-size: 16px;
    letter-spacing: .3px;
  }
  .divider {
    position: absolute;
    top: 140px;
    left: 0;
    right: 0;
    height: 1px;
    background: var(--rule);
  }
  .center-mark {
    position: absolute;
    top: 120px;
    left: 50%;
    transform: translateX(-50%);
    padding: 0 18px;
    background: #f6f6f6;
    font-weight: 700;
    font-size: 30px;
    line-height: 40px;
    color: var(--silver);
    letter-spacing: 1px;
  }
  .contact {
    position: absolute;
    top: 196px;
    left: 0;
    right: 0;
    font-style: normal;
    font-size: 15px;
    line-height: 1.45;
  }
</style>
</head>
<body>
<main class="canvas">
  <section class="business-card card-front" aria-label="Vorderseite">
    <div class="world-map" role="img" aria-label="Dezente Weltkarte aus grauen Punkten im Hintergrund"></div>
    <div class="brand">
      <span class="brand-name">KVTL</span>
      <span class="brand-web">agentur-kvtl.de</span>
    </div>
  </section>

  <section class="business-card card-back" aria-label="Rückseite">
    <h1 class="holder-name">VORNAME NAME</h1>
    <div class="divider"></div>
    <div class="center-mark">KVTL</div>
    <address class="contact">
      07146-839214-0<br>
      Name@agentur-kvtl.de<br>
      Kellberger Str. 18, 73614 Lindenfeld
    </address>
  </section>
</main>
</body>
</html>
```